Commercial Real Estate Corporate Site

Our company sells an ERP software to Commercial Real Estate Companies, this project is part of a marketing and sales relaunch of the company.

See attached for PDF formatted Design brief

The software is a modular system where client’s can adopt one module at a time. Our customers are corporate clients who own between 10M and 10B of real estate properties. The typical customer is from the IT or the Financial arm of the company. Our differentiation in the market is that our system is built on a no-code environment, so making changes for the client is quick. Incumbents in the market have long implementation cycles, and customization is often not possible. Competitors are Quorvel, TKB, PlotNest, Vumora.

We need a design for our site which will be implemented into Brevo Forge. **All designs must be compatible with the newest version of Brevo Forge.**

We have produced the following attached assets to use in the website design.:

1. Logo
2. Brand Guidelines
3. Content for Pages
4. Menu Structures
5. Illustrations (modules)
I can't attach them because the files are too big, so they're in this google drive instead:
https://files.examplestore.net/share/k29Xa7Lq0Pz3Rt8MwB5nYc4Hv1Jd6Fe?mode=view

The mechanic for our sales process is as follows:

1. We find on module from our application that a client is interested in. The illustrations that we’ve attached represent the individual modules (elements) of the software.
1. For instance, one of our current customers has purchased a commissions module from us which helps calculate the commission that brokers receive for buying and selling their properties.
2. We provide immense value through the module, and then keep in sales communication with the client to determine which other modules we can implement for them.
1. For instance, in the example above, the client is so happy with the commissions module that they want to start working with our leasing module as well. In the next business quarter, they also choose to add our financials module to their business systems.

### Logo

Attached

### Brand Guidelines

Attached

We are open to suggestions on the secondary colour palette.

### **Site Copy**

**We require the following pages to be created; For now, we will do one Market Page, one Product Page, and one Platform / Services Page, and we will use those as inspiration to create the other dozen Marketing Pages and 30 or so Product Pages.**

**Homepage**

Attached

**Market Page** - look at the quorvel site under the Office, Industrial, Retail (https://www.quorvel.com/products/quorvel-commercial-suite/)

**Product** - One product provided, but there will be 30 - look at the vumora page

(https://www.vumora.com/products/general-accounting)

**Platform / Services Page** - pages that tell the story of our platform and services, content to be provided - the platform will use our modules as it highlights the story of the configurability and composability of the platform. Instead of the icons that they use, we want to use our modules.

- https://www.pelbrix.com/enterprise-applications-platform
- https://www.pelbrix.com/cloud-architecture

**Team Page** - just add sample content for starters (6 Team Members to start)

**Schedule Demo Page** - the call to action for all pages

(https://go.vumora.com/schedule-demo.html)

### Menu Structure

The menu is provided as an attachment.

### Illustrations Information

A note about the illustrations - we have provided an illustrator file with the modules, and if you’d like you can arrange the in any way that you’d like to. We especially like when the modules are positioned like a periodic table of the elements.

Our existing clients are

- Torvane Coop - https://www.torvanecoop.com/real-estate/
- Dalsworth Realestate https://dalsworth.com

Our competitors are

- Quorvel - www.quorvel.com
- TKB - [www.tkbsoftware.com](https://www.tkbsoftware.com/) (we don’t like how this one looks)
- Vumora - www.vumora.com
- Plotnest - www.plotnest.com

Design inspiration

- https://lark-studio.brevosite.com/velmo
- Corporate
- Established
- Modern

### Stock Images Guidance

- https://www.drafta.net/design/QXR7Lm2TpWz/Hk9vN3c8Yd41-FbqsaZRr/edit?utm_content=QXR7Lm2TpWz&utm_campaign=designshare&utm_medium=link2&utm_source=sharebutton

Target Market(s)

Commercial Real Estate Companies - they typically own a portfolio of 50 - 5000 real estate properties and need a software to manage it all.

Coding

Coded - Design and coding required

Number of Pages Required

5+ page

Font styles to use
Other font styles liked:
• Fonts defined in brand guideline

Requirements
Must have
• Brevo Forge, Use the Elemental Design, Download ai.zip and png.zip Use Brand Guideline,
Nice to have
• Check design breif

```html
<!DOCTYPE html>
<html lang="en">
<head>
<meta charset="utf-8">
<title>Lumistra — Enterprise Applications Platform for Real Estate</title>
<link href="https://fonts.googleapis.com/css2?family=Audiowide&family=Montserrat:wght@400;500;600;700&family=Fira+Sans:wght@400&family=Roboto:wght@400;500&display=swap" rel="stylesheet">
<style>
:root{
  --cream:#f9f0e6;
  --red:#e30b0b;
  --deep-red:#8b0606;
  --ink:#111111;
  --dark:#121212;
  --band:#4d4d4d;
  --footer:#333333;
  --white:#ffffff;
  --muted:#d9d9d9;
}
*{margin:0;padding:0;box-sizing:border-box}
html,body{width:1200px;height:2429px;overflow:hidden}
body{position:relative;background:var(--dark);color:var(--white);font-family:"Montserrat",sans-serif}
.abs{position:absolute}
.display{font-family:"Audiowide",sans-serif;font-weight:400;text-transform:uppercase;letter-spacing:.5px}

/* header */
.site-header{left:0;top:0;width:1200px;height:62px;background:var(--cream);border-bottom:3px solid var(--red)}
.brand{display:flex;align-items:center;gap:6px;font-family:"Montserrat",sans-serif;font-weight:700;font-size:22px;color:var(--red)}
.brand-mark{width:14px;height:14px;background:var(--red)}
.site-header .brand{left:53px;top:17px}
.main-nav{left:338px;top:20px;display:flex;gap:31px;font-size:16px;font-weight:500;color:var(--ink)}
.main-nav .active{color:var(--red)}
.main-nav .has-menu::after{content:"";display:inline-block;width:5px;height:5px;border-right:2px solid var(--ink);border-bottom:2px solid var(--ink);transform:rotate(45deg);margin:0 0 3px 7px}
.btn{display:inline-flex;align-items:center;justify-content:center;background:var(--red);color:var(--white);font-weight:600}
.header-cta{left:1032px;top:15px;width:133px;height:29px;font-size:13px}

/* hero */
.hero{left:0;top:65px;width:1200px;height:433px;background:repeating-linear-gradient(90deg,#121212 0 28px,#191919 28px 29px)}
.hero-copy{left:53px;top:48px;width:600px;display:flex;flex-direction:column;align-items:flex-start}
.hero-title{font-size:23px;line-height:38px;letter-spacing:0}
.hero-text{margin-top:17px;width:540px;font-size:15px;line-height:23.5px;color:#e6e6e6}
.hero-btn{margin-top:40px;width:228px;height:38px;font-size:15px}
.hero-visual{left:660px;top:46px;width:493px;height:339px;background:linear-gradient(135deg,#f4f4f4,#bdbdbd 55%,#e8e8e8)}

.intro-band{left:42px;top:499px;width:1115px;height:91px;background:var(--band);padding:19px 39px;font-family:"Fira Sans",sans-serif;font-size:20px;line-height:24px}

/* solution */
.eyebrow{font-size:19px;font-weight:600}
.section-title{font-size:27px}
.solution-eyebrow{left:51px;top:636px}
.solution-title{left:51px;top:669px}
.card{width:257px}
.card-visual{height:113px;background:linear-gradient(135deg,#cfd8ee,#2a3fbf 60%,#0c1a7a)}
.card p{margin-top:18px;font-size:11.5px;line-height:14px;color:#e6e6e6}

/* modules */
.modules-eyebrow{left:53px;top:1021px}
.modules-title{left:53px;top:1054px}
.body-copy{font-size:15px;line-height:23.5px;color:#e6e6e6}
.body-copy p+p{margin-top:13px}
.modules-copy{left:53px;top:1110px;width:545px}
.periodic-visual{left:695px;top:1020px;width:410px;height:305px;background:linear-gradient(160deg,#2d6a6a,#c98a34 45%,#3d7a42 70%,#d4d4d4)}

.settle-title{left:51px;top:1403px;font-size:27px}
.settle-copy{left:51px;top:1461px;width:610px}
.cube-grid{left:812px;top:1470px;display:grid;grid-template-columns:repeat(3,42px);column-gap:75px;row-gap:52px}
.cube{width:42px;height:42px;border-radius:3px}

/* about */
.about{left:53px;top:1795px;width:1065px;height:263px;display:flex}
.about-panel{width:597px;background:var(--deep-red);padding:26px 24px}
.about-panel h2{font-size:27px}
.about-panel p{margin-top:14px;font-size:15px;line-height:23.5px;width:540px}
.about-btn{margin-top:14px;width:130px;height:39px;font-size:15px}
.about-brand{flex:1;background:var(--cream);display:flex;align-items:center;justify-content:center}
.about-brand .brand{font-size:64px;gap:18px}
.about-brand .brand-mark{width:56px;height:56px}

/* footer */
.site-footer{left:0;top:2140px;width:1200px;height:254px;background:var(--footer)}
.site-footer .brand{left:81px;top:60px;color:var(--white);font-size:26px}
.site-footer .brand-mark{background:var(--white);width:18px;height:18px}
.footer-tagline{left:81px;top:116px;width:220px;font-size:17px;font-weight:600;line-height:20px}
.footer-col{top:60px;font-family:"Roboto",sans-serif}
.footer-col h3{font-size:20px;font-weight:500;margin-bottom:18px}
.footer-col li{list-style:none;font-size:14px;line-height:26.5px}
.copyright{left:0;top:2394px;width:1200px;height:35px;background:var(--red);display:flex;align-items:center;justify-content:center;font-size:14px}
</style>
</head>
<body>

<header class="site-header abs">
  <div class="brand abs"><span class="brand-mark"></span>Lumistra</div>
  <nav class="main-nav abs">
    <span class="active">Home</span>
    <span class="has-menu">Market</span>
    <span class="has-menu">Platform</span>
    <span class="has-menu">Resources</span>
    <span>About Us</span>
  </nav>
  <a class="btn header-cta abs">Contact Us</a>
</header>

<section class="hero abs">
  <div class="hero-copy abs">
    <h1 class="hero-title display">Welcome to Lumistra — an infinitely composable enterprise applications platform (EAP) for real estate.</h1>
    <p class="hero-text">Far beyond what’s possible with tired, legacy real estate ERP software, Lumistra offers a complete industry solution, architected as flexible modules that can be assembled and configured into an infinite combination of processes and workflows.</p>
    <a class="btn hero-btn">Explore more about us</a>
  </div>
  <div class="hero-visual abs" role="img" aria-label="White architectural corridor with glowing angular light lines"></div>
</section>

<div class="intro-band abs">The Lumistra Enterprise solution seamlessly delivers both modular software and bundled services to transform your business with less risk, greater security, and lower cost.</div>

<div class="eyebrow solution-eyebrow abs">Lumistra Enterprise</div>
<h2 class="section-title display solution-title abs">One Solution - Infinite Possibilities</h2>

<article class="card abs" style="left:51px;top:729px">
  <div class="card-visual" role="img" aria-label="Facade of silver discs on deep blue architecture"></div>
  <p>Lumistra was born from decades of real estate enterprise software development and implementation experience — spanning hundreds of blue chip global real estate investment firms. But Lumistra is unlike anything you’ve experienced before.</p>
</article>
<article class="card abs" style="left:331px;top:729px">
  <div class="card-visual" role="img" aria-label="Curved white building against a blue sky"></div>
  <p>No more multi-million-dollar disruptive implementations. No more waiting for upgrades and enhancements that never come. No more trailing projects and disappointing customizations. No more settling for less than exactly what you want.</p>
</article>
<article class="card abs" style="left:611px;top:729px">
  <div class="card-visual" style="background:linear-gradient(135deg,#1b3fd6,#2d6cf0 50%,#0a1f8a)" role="img" aria-label="Blue-lit modern interior with curved ceiling"></div>
  <p>You can begin using Lumistra simply — starting with a single module. Then, you can build-on with additional modules at your own pace.</p>
</article>
<article class="card abs" style="left:890px;top:729px">
  <div class="card-visual" style="background:linear-gradient(135deg,#0d2a5c,#3a6fb0 55%,#0a1a3a)" role="img" aria-label="Modern pavilion with city skyline at dusk"></div>
  <p>Lumistra Enterprise combines software and services in a simple, annual subscription.</p>
</article>

<div class="eyebrow modules-eyebrow abs">The Modules of Lumistra</div>
<h2 class="section-title display modules-title abs">Simple - Secure - Scalable</h2>
<div class="body-copy modules-copy abs">
  <p>Lumistra is the real estate industry’s only infinitely composable Enterprise Applications Platform (EAP), ensuring scalability, security, auditability, and compliance. Lumistra is a complete solution covering all functional areas of real estate investment, development, finance, accounting, management and operations.</p>
  <p>No more business disruption, downtime, high costs, diminishing ROI, and inflexibility. Run your business your way, break the cycle of technical debt, and focus on high-value, innovative opportunities.</p>
</div>
<div class="periodic-visual abs" role="img" aria-label="Module blocks arranged like a periodic table in teal, orange, green and grey"></div>

<h2 class="display settle-title abs">Stop settling for less than exactly what you want</h2>
<div class="body-copy settle-copy abs">
  <p>Lumistra combines the best of all worlds in our Enterprise Applications Platform (EAP): the simplicity and scalability of custom, no-code, software and the security and confidence of a complete, SOC 2 compliant industry solution. Our modular approach enables rapid innovation and re-invention of your business by casting off the shackles of legacy ERP technology and delivering a modern, agile solution that bridges the gaps for all of your real estate workflows.</p>
  <p>No more closed systems, complicated integrations, overreliance on spreadsheets, and complex or unavailable customizations. In their place is Lumistra’ robust set of preconfigured yet flexible capabilities that can be deployed as point-solutions or to compose larger business processes.</p>
</div>
<div class="cube-grid abs">
  <div class="cube" style="background:#c98a34" role="img" aria-label="Orange module block"></div>
  <div class="cube" style="background:#8a8a8a" role="img" aria-label="Grey module block"></div>
  <div class="cube" style="background:#2b5f66" role="img" aria-label="Teal module block"></div>
  <div class="cube" style="background:#1f6b62" role="img" aria-label="Dark teal module block"></div>
  <div class="cube" style="background:#3d7a42" role="img" aria-label="Green module block"></div>
  <div class="cube" style="background:#2d5a6e" role="img" aria-label="Blue-teal module block"></div>
  <div class="cube" style="background:#d8d8d8" role="img" aria-label="White module block"></div>
  <div class="cube" style="background:#d0d0d0" role="img" aria-label="White module block"></div>
  <div class="cube" style="background:#777777" role="img" aria-label="Dark grey module block"></div>
</div>

<section class="about abs">
  <div class="about-panel">
    <h2 class="display">About Us</h2>
    <p>Lumistra is the real estate industry’s modern alternative to rigid, legacy ERP systems. With decades of real estate enterprise software development and implementation expertise — spanning hundreds of blue chip global real estate investment firms — we have a proven track record of enterprise excellence.</p>
    <a class="btn about-btn">Learn More</a>
  </div>
  <div class="about-brand">
    <div class="brand"><span class="brand-mark"></span>Lumistra</div>
  </div>
</section>

<footer class="site-footer abs">
  <div class="brand abs"><span class="brand-mark"></span>Lumistra</div>
  <p class="footer-tagline abs">Transform your business with less risk, greater security, and lower cost.</p>
  <div class="footer-col abs" style="left:502px">
    <h3>Information</h3>
    <ul><li>Privacy Policy</li><li>Payment Method</li><li>Refund Policy</li><li>Terms of use</li></ul>
  </div>
  <div class="footer-col abs" style="left:668px">
    <h3>Services</h3>
    <ul><li>Privacy Policy</li><li>Payment Method</li><li>Refund Policy</li><li>Shopping</li></ul>
  </div>
  <div class="footer-col abs" style="left:835px">
    <h3>Navigation</h3>
    <ul><li>Home</li><li>Contact</li><li>Services</li></ul>
  </div>
  <div class="footer-col abs" style="left:991px">
    <h3>Our Company</h3>
    <ul><li>About Us</li><li>Contact Information</li></ul>
  </div>
</footer>
<div class="copyright abs">@ Copyright 2024 Lumistra</div>

</body>
</html>
```